need eczema bath soak label/bag

need you to recreate this please. ai file. recreate this exact image please. ...if you want a big tip, create some different styles.

Colors
0054AA
0677BA
7BADD7
CADEEF
E8F1F8

```html
<!DOCTYPE html>
<html lang="en">
<head>
<meta charset="UTF-8">
<title>The Ocean Healed Soak – Bath Soak Label</title>
<link rel="stylesheet" href="https://fonts.googleapis.com/css2?family=Montserrat:wght@400;500;700;800&display=swap">
<style>
  :root {
    --backdrop: #021a2c;
    --ink: #2a3440;
    --paper: #fbfcfd;
    --mist: #e8f1f8;
    --pale-sea: #cadeef;
    --sea-light: #7badd7;
    --sea-teal: #2f9cba;
    --sea-deep: #0677ba;
    --foam: #f2f5f6;
    --wet-sand: #d9d2c0;
    --dry-sand: #d8bd88;
    --sand-light: #e3cfa4;
  }
  * { margin: 0; padding: 0; box-sizing: border-box; }
  html, body {
    width: 1200px;
    height: 800px;
    overflow: hidden;
    background: var(--backdrop);
  }
  .canvas {
    position: relative;
    width: 1200px;
    height: 800px;
    background: var(--backdrop);
  }
  .label {
    position: absolute;
    left: 395px;
    top: 76px;
    width: 410px;
    height: 648px;
    border-radius: 14px;
    overflow: hidden;
    background: var(--paper);
    font-family: 'Montserrat', sans-serif;
    color: var(--ink);
  }
  .shore-scene {
    position: absolute;
    inset: 0;
    background: linear-gradient(
      to bottom,
      var(--paper) 0%,
      var(--paper) 28%,
      var(--mist) 32%,
      var(--sea-light) 36%,
      var(--sea-teal) 42%,
      var(--sea-deep) 50%,
      var(--sea-teal) 56%,
      var(--pale-sea) 62%,
      var(--foam) 68%,
      var(--wet-sand) 74%,
      var(--foam) 80%,
      var(--sand-light) 84%,
      var(--dry-sand) 100%
    );
  }
  .line {
    position: absolute;
    left: 0;
    right: 0;
    text-align: center;
    line-height: 1;
  }
  .title-the {
    top: 141px;
    font-size: 20px;
    font-weight: 800;
  }
  .title-word {
    font-size: 54px;
    font-weight: 800;
    letter-spacing: -0.5px;
  }
  .title-ocean { top: 176px; }
  .title-healed { top: 235px; }
  .title-soak { top: 292px; }
  .claim {
    top: 350px;
    left: 95px;
    right: 95px;
    font-size: 12.5px;
    font-weight: 400;
    line-height: 1.3;
  }
  .treatment {
    top: 411px;
    font-size: 13.5px;
    font-weight: 700;
  }
  .weight {
    top: 438px;
    font-size: 16px;
    font-weight: 700;
  }
  .product-type {
    top: 466px;
    font-size: 11px;
    font-weight: 400;
  }
  .brand-name {
    top: 588px;
    font-size: 12px;
    font-weight: 700;
    letter-spacing: 3px;
  }
</style>
</head>
<body>
  <main class="canvas">
    <section class="label">
      <div class="shore-scene" role="img" aria-label="Aerial photograph of turquoise ocean waves washing onto a sandy beach, fading to white at the top"></div>

      <p class="line title-the">THE</p>
      <h1>
        <span class="line title-word title-ocean">OCEAN</span>
        <span class="line title-word title-healed">HEALED</span>
        <span class="line title-word title-soak">SOAK</span>
      </h1>

      <p class="line claim">bath soak to relieve symptoms of mid eczema &amp; itchy, irritated, dry skin</p>
      <p class="line treatment">SOOTHING TREATMENT</p>
      <p class="line weight">170g/60oz</p>
      <p class="line product-type">BATH SOAK</p>

      <p class="line brand-name">TIDEWELL</p>
    </section>
  </main>
</body>
</html>
```